Tolvik Commercial Cleaning is lookong for a new business card design.

A fresh new design that's professional and stylish. We need a serious upgrade to our business cards. I have included pictures of our existing ones. Our clients include professional individuals and business owners. We woupdblike something professional and upbeat. Please have fun and see what you come uo with.

Target Market(s)

Property managers, business owners, facility managers and other similar professionals

Industry/Entity Type

Janitorial

Contact Information for Business Card

Name, cell, office number, email, web address

Font styles to use
Sans Serif

Colors

Designer to choose colors to be used in the design.

Requirements
Must have
• please use the green color in our logo
Nice to have
• Bar code
Should not have
• Address

```html
<!DOCTYPE html>
<html lang="en">
<head>
<meta charset="utf-8">
<title>Tolvik Commercial Cleaning – Business Card</title>
<link rel="stylesheet" href="https://fonts.googleapis.com/css2?family=Open+Sans:wght@400;600;700&display=swap">
<style>
  :root {
    --card: #222327;
    --green: #3ab54a;
    --blue: #3f72b5;
    --white: #ffffff;
    --stage: #e9e9e7;
  }
  * { box-sizing: border-box; margin: 0; padding: 0; }
  html, body { width: 1200px; height: 780px; overflow: hidden; }
  body {
    background: var(--stage);
    font-family: "Open Sans", Arial, sans-serif;
    display: flex;
    align-items: center;
    justify-content: center;
    gap: 80px;
  }
  .card {
    position: relative;
    width: 300px;
    height: 525px;
    background: var(--card);
    border-radius: 22px;
    box-shadow: 0 0 0 3px var(--green), 0 10px 24px rgba(0,0,0,.25);
    overflow: hidden;
  }

  /* Front */
  .front .brand {
    position: absolute;
    left: 50%;
    top: 50%;
    width: 460px;
    transform: translate(-50%, -50%) rotate(90deg);
    color: var(--green);
    font-weight: 700;
    text-align: center;
    line-height: 1;
  }
  .front .brand-name { display: block; font-size: 104px; letter-spacing: -2px; }
  .front .brand-line { display: block; font-size: 33px; margin-top: 10px; }

  /* Back */
  .back .brand {
    position: absolute;
    top: 58px;
    left: 0;
    right: 0;
    text-align: center;
    color: var(--green);
    font-weight: 700;
    line-height: 1.05;
  }
  .back .brand-name { display: block; font-size: 56px; letter-spacing: -1px; }
  .back .brand-line { display: block; font-size: 17px; margin-top: 6px; }

  .contact {
    position: absolute;
    left: 0;
    right: 0;
    bottom: 56px;
    text-align: right;
    padding-right: 28px;
  }
  .person-name { font-size: 27px; font-weight: 700; line-height: 1; }
  .person-name .first { color: var(--green); }
  .person-name .last { color: var(--blue); }
  .person-role { color: var(--white); font-size: 14px; font-weight: 600; margin-top: 4px; }

  .divider {
    display: flex;
    align-items: center;
    justify-content: flex-end;
    gap: 5px;
    margin: 12px -10px 12px 0;
  }
  .dot { display: block; border-radius: 50%; background: var(--green); }
  .icon {
    width: 24px; height: 24px;
    border-radius: 50%;
    background: var(--green);
    display: flex; align-items: center; justify-content: center;
  }
  .icon svg { width: 14px; height: 14px; }

  .details { list-style: none; color: var(--white); font-size: 14px; line-height: 1.5; }
</style>
</head>
<body>

  <section class="card front" aria-label="Card front">
    <p class="brand"><span class="brand-name">Tolvik</span><span class="brand-line">Commercial Cleaning</span></p>
  </section>

  <section class="card back" aria-label="Card back">
    <p class="brand"><span class="brand-name">Tolvik</span><span class="brand-line">Commercial Cleaning</span></p>

    <div class="contact">
      <h1 class="person-name"><span class="first">Maren</span> <span class="last">Holt</span></h1>
      <p class="person-role">Director</p>

      <div class="divider" aria-hidden="true">
        <span class="dot" style="width:4px;height:4px"></span>
        <span class="dot" style="width:6px;height:6px"></span>
        <span class="dot" style="width:8px;height:8px"></span>
        <span class="dot" style="width:10px;height:10px"></span>
        <span class="dot" style="width:12px;height:12px"></span>
        <span class="icon"><svg viewBox="0 0 24 24"><path fill="#fff" d="M6.6 10.8a15 15 0 0 0 6.6 6.6l2.2-2.2c.3-.3.7-.4 1-.2 1.1.4 2.3.6 3.6.6.6 0 1 .4 1 1V20c0 .6-.4 1-1 1C10.6 21 3 13.4 3 4c0-.6.4-1 1-1h3.5c.6 0 1 .4 1 1 0 1.3.2 2.5.6 3.6.1.3 0 .7-.2 1z"/></svg></span>
        <span class="icon"><svg viewBox="0 0 24 24"><path fill="#fff" d="M3 6h18v12H3z"/><path fill="none" stroke="#3ab54a" stroke-width="2" d="M3 6l9 7 9-7"/></svg></span>
        <span class="icon"><svg viewBox="0 0 24 24"><circle cx="12" cy="12" r="9" fill="none" stroke="#fff" stroke-width="2"/><path fill="none" stroke="#fff" stroke-width="1.6" d="M3 12h18M12 3c3 3 3 15 0 18M12 3c-3 3-3 15 0 18"/></svg></span>
        <span class="dot" style="width:12px;height:12px"></span>
        <span class="dot" style="width:10px;height:10px"></span>
        <span class="dot" style="width:8px;height:8px"></span>
        <span class="dot" style="width:6px;height:6px"></span>
        <span class="dot" style="width:4px;height:4px"></span>
      </div>

      <ul class="details">
        <li>(555) 014-2290</li>
        <li>maren@tolvikcleaning.com</li>
        <li>www.tolvikcleaning.com</li>
      </ul>
    </div>
  </section>

</body>
</html>
```